Brochure design for International Beauty Trade Show

I neee a tri-fold company products' brochure to distribute to customers at an international trade show coming soon. We have 4 main product categories- hair and skincare, facial care, Body and bath and massage oil.
The brochure needs to include at least 2 photos of the main products of each category, benefits, call to action and our company contact info ( website and phone number).

Target Market(s)

Educated and high income earners looking for all-natural,pure, 100 organic products for their beauty and personal care needs. Our products cross all racial groups/demographics and suitable for all skin types

Industry/Entity Type

Hair And Beauty

Font styles to use
Serif

Colors

Designer to choose colors to be used in the design.

Requirements
Must have
• The design must stand out as pure and luxury and at the same time be inclusive using our logo design colors- orange and blue. Also, the content must be easy to read and captivating.
• Finally if using women pictures, please include Black, white, Asian and Latina to reflect the fact that our products are suitable for all skin types.
Nice to have
• Design the brochure such that it could be printed as a poster-banner ad.
Should not have
• Cookie cutter designs are not welcome

```html
<!DOCTYPE html>
<html lang="en">
<head>
<meta charset="utf-8">
<title>Lumeva Solutions – Trifold Brochure Outside</title>
<link href="https://fonts.googleapis.com/css2?family=Cinzel:wght@400;600&family=Exo+2:wght@400;500;600;700&display=swap" rel="stylesheet">
<style>
  :root{
    --page:#e8e8ea;
    --navy:#0b1f4f;
    --blue:#1a4a9c;
    --blue-deep:#0f2f70;
    --orange:#e8661c;
    --purple:#4a1457;
    --plum:#5e1356;
    --gold:#e9d39a;
    --white:#ffffff;
    --ink-light:#eef2fb;
  }
  *{box-sizing:border-box;margin:0;padding:0}
  html,body{width:1200px;height:919px;overflow:hidden;background:var(--page)}
  .brochure{position:absolute;left:30px;top:56px;width:1140px;height:806px;overflow:hidden;font-family:"Exo 2",sans-serif}
  .brochure-art{position:absolute;inset:0}
  .abs{position:absolute}
  .frame-title{font-family:"Cinzel",serif;font-weight:400;border:1px solid currentColor;border-radius:6px;padding:3px 12px;white-space:nowrap;transform:translate(-50%,-50%)}
  .massage-title{left:194px;top:99px;color:var(--purple);font-size:20px;background:rgba(255,255,255,.6)}
  .massage-rule{left:86px;top:99px;width:215px;height:1px;background:var(--purple)}
  .benefits{left:24px;top:432px;list-style:none}
  .benefits li{display:flex;align-items:center;height:31px;margin-bottom:5px;color:var(--purple);font-weight:500;font-size:17px}
  .benefits .arrow{width:16px;height:16px;flex:none;margin-right:6px}
  .benefits span{border:1px dotted #7a4a86;border-radius:6px;padding:3px 7px}
  .contact{line-height:1}
  .contact .phone{display:flex;align-items:center;gap:8px;color:var(--gold);font-size:25px;font-weight:500;margin-bottom:10px}
  .contact .line{display:flex;align-items:center;gap:9px;color:var(--white);font-size:19px;margin-bottom:6px;margin-left:14px}
  .contact svg{flex:none}
  .contact-left{left:88px;top:707px}
  .contact-mid{left:456px;top:706px}
  .about-title{left:570px;top:42px;color:var(--white);font-size:24px}
  .about-text{left:411px;top:89px;width:318px;color:var(--ink-light);font-size:15.2px;line-height:24.4px;text-align:justify;text-align-last:center;hyphens:auto}
  .contact-title{left:570px;top:665px;color:var(--white);font-size:17px}
  .seal{left:477px;top:404px;width:192px;height:192px;border-radius:50%;display:flex;align-items:center;justify-content:center;color:var(--blue);font-weight:600;font-size:30px}
  .brand{left:960px;top:480px;width:170px;text-align:center;color:var(--blue);font-weight:600;font-size:22px}
  .headline{left:782px;top:606px;color:var(--white);line-height:1}
  .headline .l1{font-size:38px;font-weight:400;margin-bottom:6px}
  .headline .l2{font-size:38px;font-weight:400;margin-bottom:5px}
  .headline .l3{font-size:50px;font-weight:400;color:var(--orange);margin-bottom:4px;letter-spacing:1px}
  .headline .l4{font-size:52px;font-weight:700;color:var(--gold);letter-spacing:1px}
</style>
</head>
<body>
<main class="brochure">
  <svg class="brochure-art" width="1140" height="806" viewBox="0 0 1140 806">
    <defs>
      <linearGradient id="leftPaper" x1="0" y1="0" x2="0" y2="1"><stop offset="0" stop-color="#f7f7f9"/><stop offset="1" stop-color="#e4e4e8"/></linearGradient>
      <radialGradient id="midNight" cx="0.5" cy="0.4" r="0.8"><stop offset="0" stop-color="#16357a"/><stop offset="1" stop-color="#071638"/></radialGradient>
      <linearGradient id="blueBand" x1="0" y1="0" x2="0" y2="1"><stop offset="0" stop-color="#1d54aa"/><stop offset="1" stop-color="#0f2f70"/></linearGradient>
      <linearGradient id="portraitTone" x1="0" y1="0" x2="1" y2="1"><stop offset="0" stop-color="#101c4a"/><stop offset="0.55" stop-color="#3a2a55"/><stop offset="1" stop-color="#c99a86"/></linearGradient>
      <linearGradient id="productTone" x1="0" y1="0" x2="1" y2="1"><stop offset="0" stop-color="#f3f3f6"/><stop offset="0.5" stop-color="#d9d6e0"/><stop offset="1" stop-color="#b54b4b" stop-opacity=".45"/></linearGradient>
      <linearGradient id="silver" x1="0" y1="0" x2="0" y2="1"><stop offset="0" stop-color="#ffffff"/><stop offset="1" stop-color="#9aa2ad"/></linearGradient>
    </defs>

    <!-- left panel -->
    <rect x="0" y="0" width="380" height="806" fill="url(#leftPaper)"/>
    <path d="M0 0H380V58C260 28 100 48 0 118Z" fill="var(--plum)"/>
    <path d="M0 132C100 62 270 38 380 66" fill="none" stroke="var(--orange)" stroke-width="8"/>
    <rect x="56" y="142" width="236" height="276" rx="6" fill="url(#productTone)" role="img" aria-label="Massage oil bottle with red berries"/>
    <path d="M0 748C120 642 262 574 380 536" fill="none" stroke="var(--orange)" stroke-width="12"/>
    <path d="M0 730C120 624 262 556 380 518V806H0Z" fill="url(#blueBand)"/>

    <!-- middle panel -->
    <rect x="380" y="0" width="380" height="806" fill="url(#midNight)"/>
    <path d="M380 528Q570 462 760 528" fill="none" stroke="#dfe6f3" stroke-width="10"/>
    <path d="M380 536Q570 470 760 536V806H380Z" fill="url(#blueBand)"/>
    <circle cx="573" cy="500" r="98" fill="url(#silver)"/>
    <circle cx="573" cy="500" r="89" fill="var(--white)"/>

    <!-- right panel -->
    <rect x="760" y="0" width="380" height="620" fill="url(#portraitTone)" role="img" aria-label="Portrait of a woman with dark hair and magenta nails"/>
    <path d="M760 512C900 512 1050 464 1140 362" fill="none" stroke="var(--orange)" stroke-width="9"/>
    <path d="M760 520C900 520 1050 472 1140 372V806H760Z" fill="#f3f4f7"/>
    <path d="M760 538C920 556 1060 676 1140 786V806H760Z" fill="url(#blueBand)"/>
    <path d="M852 556C980 586 1080 676 1140 752" fill="none" stroke="var(--orange)" stroke-width="2"/>
    <circle cx="1045" cy="458" r="36" fill="var(--orange)"/>
  </svg>

  <!-- left panel content -->
  <div class="abs massage-rule"></div>
  <h2 class="abs frame-title massage-title">Massage Care</h2>
  <ul class="abs benefits">
    <li><svg class="arrow" viewBox="0 0 16 16"><circle cx="8" cy="8" r="8" fill="var(--purple)"/><path d="M4 8h7M8 5l3 3-3 3" stroke="#fff" stroke-width="1.6" fill="none"/></svg><span>Relief stress and pain</span></li>
    <li><svg class="arrow" viewBox="0 0 16 16"><circle cx="8" cy="8" r="8" fill="var(--purple)"/><path d="M4 8h7M8 5l3 3-3 3" stroke="#fff" stroke-width="1.6" fill="none"/></svg><span>Fight muscle contraction/tenderness</span></li>
    <li><svg class="arrow" viewBox="0 0 16 16"><circle cx="8" cy="8" r="8" fill="var(--purple)"/><path d="M4 8h7M8 5l3 3-3 3" stroke="#fff" stroke-width="1.6" fill="none"/></svg><span>Eliminate stretch marks</span></li>
    <li><svg class="arrow" viewBox="0 0 16 16"><circle cx="8" cy="8" r="8" fill="var(--purple)"/><path d="M4 8h7M8 5l3 3-3 3" stroke="#fff" stroke-width="1.6" fill="none"/></svg><span>Pure, undiluted</span></li>
  </ul>
  <div class="abs contact contact-left">
    <div class="phone"><svg width="16" height="16" viewBox="0 0 16 16"><circle cx="8" cy="8" r="8" fill="var(--orange)"/><path d="M5.5 4.5l1.5 1.5-1 1a5 5 0 003 3l1-1 1.5 1.5-1.2 1.2C7.5 12.5 3.5 8.5 4.3 5.7z" fill="#fff"/></svg>(800) 555-0147</div>
    <div class="line"><svg width="15" height="15" viewBox="0 0 16 16"><circle cx="8" cy="8" r="8" fill="var(--orange)"/><rect x="4" y="5" width="8" height="6" fill="none" stroke="#fff"/><path d="M4 5l4 3 4-3" stroke="#fff" fill="none"/></svg>hello@lumeva.com</div>
    <div class="line"><svg width="15" height="15" viewBox="0 0 16 16"><circle cx="8" cy="8" r="8" fill="var(--orange)"/><rect x="4" y="5" width="8" height="5" fill="none" stroke="#fff"/><path d="M3.5 11.5h9" stroke="#fff"/></svg>www.lumeva.com</div>
  </div>

  <!-- middle panel content -->
  <h2 class="abs frame-title about-title">About Us</h2>
  <p class="abs about-text">Our company is committed to corporate social responsibility as we continue to develop business solutions that deliver enduring value to our customers and contribute to sponsoring sustainable economic and social growth. We are determined to promote environmentally sound and vibrant communities around the world via the transfer of knowledge and technologies, fair and equitable treatment of all constituents.</p>
  <div class="abs seal">Lumeva</div>
  <h2 class="abs frame-title contact-title">Contact Info:</h2>
  <div class="abs contact contact-mid">
    <div class="phone"><svg width="16" height="16" viewBox="0 0 16 16"><circle cx="8" cy="8" r="8" fill="var(--orange)"/><path d="M5.5 4.5l1.5 1.5-1 1a5 5 0 003 3l1-1 1.5 1.5-1.2 1.2C7.5 12.5 3.5 8.5 4.3 5.7z" fill="#fff"/></svg>(800) 555-0147</div>
    <div class="line"><svg width="15" height="15" viewBox="0 0 16 16"><circle cx="8" cy="8" r="8" fill="var(--orange)"/><rect x="4" y="5" width="8" height="6" fill="none" stroke="#fff"/><path d="M4 5l4 3 4-3" stroke="#fff" fill="none"/></svg>hello@lumeva.com</div>
    <div class="line"><svg width="15" height="15" viewBox="0 0 16 16"><circle cx="8" cy="8" r="8" fill="var(--orange)"/><rect x="4" y="5" width="8" height="5" fill="none" stroke="#fff"/><path d="M3.5 11.5h9" stroke="#fff"/></svg>www.lumeva.com</div>
  </div>

  <!-- right panel content -->
  <div class="abs brand">Lumeva Solutions</div>
  <h1 class="abs headline">
    <div class="l1">Natural</div>
    <div class="l2">Solutions to</div>
    <div class="l3">FOREVER</div>
    <div class="l4">BEAUTY</div>
  </h1>
</main>
</body>
</html>
```